Website Design Required For Education Video Portfolio Site

I am looking for a designer to create a skin for a relaunch of my website - www.brackenlearningfilms.co.uk. We want a clean and stylish new design.

The website showcases prospectus/promotional videos that are made for schools and colleges. Videos will be hosted on YouTube and embedded.

I want it to be stylish and clean.

I require 7 pages designed and this must be agreed in order to do the project.

1. Homepage
2. About
3. Prices
4. Testimonials
5. Contact Page with form
6. Promotional Videos
7. Subject Videos

The website will be then be built on the Wordpress system.

Target Market(s)

Education, Schools, Colleges, Universities

Industry/Entity Type

Education

Font styles to use
Serif

Colors

Designer to choose colors to be used in the design.

Requirements
Must have
• Video content, be clean, show our portfolio, descriptions about videos. I like the idea of having video headers.
Nice to have
• Images

```html
<!DOCTYPE html>
<html lang="en">
<head>
<meta charset="utf-8">
<title>Bracken Learning Films</title>
<link href="https://fonts.googleapis.com/css2?family=Mulish:wght@300;400;600;700&display=swap" rel="stylesheet">
<style>
:root{
  --blue:#1db0ee;
  --blue-dark:#0d8fd0;
  --ink:#1f1f1f;
  --text:#333;
  --muted:#555;
  --white:#fff;
  --black:#0b0b0b;
}
*{box-sizing:border-box;margin:0;padding:0}
html,body{width:1200px;height:4484px;overflow:hidden}
body{font-family:'Mulish',sans-serif;color:var(--text);background:var(--white);position:relative}
section,footer,header{position:absolute;left:0;width:1200px}
.abs{position:absolute}
.media{position:absolute}
h2{font-weight:700;color:var(--ink);font-size:36px;line-height:1.35;text-align:center}
h2 span{display:block;font-weight:300}
p{font-size:14px;line-height:28px}

/* hero */
.hero{top:0;height:514px;background:linear-gradient(180deg,#4a4640 0%,#5d5a48 45%,#3f4a30 100%)}
.menu-icon{left:110px;top:52px;width:44px}
.menu-icon i{display:block;height:3px;background:var(--white);margin-bottom:7px}
.brand{left:505px;top:38px;display:flex;align-items:center;gap:10px;color:var(--blue);font-weight:700;font-size:30px}
.brand b{width:34px;height:34px;background:var(--blue);border-radius:8px;display:block}
.quote-btn{left:955px;top:35px;width:134px;height:44px;border:1.5px solid var(--white);border-radius:4px;color:var(--white);font-size:13px;display:flex;align-items:center;justify-content:center}
.hero-title{top:192px;width:100%;text-align:center;color:var(--white);font-size:36px;line-height:54px}
.hero-title strong{font-weight:700;display:block}
.hero-title span{font-weight:300}
.scroll-btn{left:569px;top:404px}

/* intro */
.intro{top:514px;height:599px}
.intro h2{position:absolute;top:60px;width:100%}
.intro .copy{left:111px;top:240px;width:450px}
.intro .copy p{font-size:15px;margin-bottom:8px}
.intro-video{left:608px;top:197px;width:592px;height:320px;background:var(--blue);border-radius:28px 0 0 28px}
.intro-video .media{left:10px;top:10px;right:0;bottom:10px;border-radius:24px 0 0 24px;background:linear-gradient(135deg,#8c2f4a,#a8385a 50%,#7b2a40)}
.video-label{position:absolute;left:60px;bottom:26px;color:var(--white);font-size:22px;line-height:22px}
.video-label strong{display:block;font-weight:700}

/* investment */
.invest{top:1113px;height:570px;background:var(--blue)}
.invest .media{left:0;top:0;width:538px;height:570px;background:linear-gradient(160deg,#5b8f8e,#c9a98f 55%,#8a6a52)}
.invest .body{left:617px;top:50px;width:475px;color:var(--white)}
.invest h3{font-size:36px;line-height:50px;font-weight:700;margin-bottom:28px}
.invest h3 span{display:block;font-weight:300}
.invest p{font-size:14px;line-height:28px;margin-bottom:10px}
.btn-dark{display:inline-flex;align-items:center;justify-content:center;width:204px;height:42px;background:#111;color:var(--white);border-radius:5px;font-size:14px;margin-top:14px}

/* why */
.why{top:1683px;height:674px}
.why h2{position:absolute;top:64px;width:100%}
.card{position:absolute;top:216px;width:247px;height:392px;background:var(--white);border-radius:10px;box-shadow:4px 10px 26px rgba(0,0,0,.13);padding:122px 18px 0 18px}
.card .badge{position:absolute;left:0;top:-12px;width:130px;height:110px;background:var(--blue);border-radius:10px 0 110px 0}
.card .badge svg{position:absolute;left:20px;top:22px}
.card h4{font-size:16px;font-weight:400;line-height:28px;color:var(--ink);margin-bottom:10px}
.card p{font-size:14px;line-height:26px;color:var(--muted)}
.card .go{position:absolute;left:18px;bottom:28px}

/* budget band */
.budget{top:2357px;height:345px;background:linear-gradient(90deg,#2f3035,#4a4b50 60%,#3b3b40)}
.budget h3{position:absolute;left:111px;top:70px;color:var(--white);font-size:36px;line-height:50px;font-weight:700}
.budget h3 span{display:block;font-weight:300}
.budget p{position:absolute;left:111px;top:206px;width:660px;color:var(--white);font-size:14px}
.btn-blue{position:absolute;left:876px;top:216px;width:212px;height:44px;background:var(--blue);color:var(--white);border-radius:5px;font-size:14px;display:flex;align-items:center;justify-content:center}

/* custom */
.custom{top:2702px;height:560px}
.custom h2{position:absolute;top:72px;width:100%}
.custom-video{left:0;top:211px;width:590px;height:320px;background:var(--blue);border-radius:0 28px 28px 0}
.custom-video .media{left:0;top:0;right:10px;bottom:10px;border-radius:0 24px 24px 0;background:linear-gradient(150deg,#5f7a3e,#7c8f55 50%,#4e5f35)}
.custom .copy{left:646px;top:208px;width:440px}
.custom .copy p{margin-bottom:14px}
.custom .copy a{color:var(--blue-dark);text-decoration:underline}
.btn-outline{display:inline-flex;align-items:center;justify-content:center;width:212px;height:42px;border:1.5px solid #555;border-radius:5px;font-size:14px;color:var(--ink);text-decoration:none!important}

/* drone */
.drone{top:3262px;height:430px}
.drone .box{left:111px;top:97px;width:978px;height:308px;background:var(--blue);border-radius:10px;color:var(--white);text-align:center;padding-top:88px}
.drone h3{font-size:36px;font-weight:700;line-height:50px;margin-bottom:18px}
.drone .box p{font-size:34px;font-weight:300;line-height:50px}
.drone .media{left:830px;top:10px;width:360px;height:170px;border-radius:50%;background:radial-gradient(ellipse at center,rgba(60,62,68,.55) 0%,rgba(120,122,128,.3) 45%,rgba(255,255,255,0) 70%)}

/* partners */
.partners{top:3692px;height:440px}
.partners h2{position:absolute;top:78px;width:100%}
.arrow{position:absolute;top:282px}
.partner{position:absolute;top:242px;height:110px;display:flex;align-items:center;gap:10px;font-size:24px;font-weight:700;color:var(--ink)}
.partner b{display:block;background:var(--blue);border-radius:50%}

/* footer */
footer{top:4132px;height:352px;background:var(--black);color:var(--white)}
.contact{position:absolute;top:72px;display:flex;gap:16px;font-size:16px;line-height:30px}
.rule{position:absolute;left:111px;width:978px;height:1px;background:#333}
.foot-nav{position:absolute;top:210px;width:100%;display:flex;justify-content:center;gap:36px;font-size:16px}
.copyright{position:absolute;left:118px;top:306px;font-size:13px}
.social{position:absolute;left:1060px;top:296px;width:30px;height:30px;border:1.5px solid var(--white);border-radius:50%}
</style>
</head>
<body>

<header class="hero" role="img" aria-label="Video header: children gardening in a school playground">
  <div class="abs menu-icon"><i></i><i></i></div>
  <div class="abs brand"><b></b>Bracken</div>
  <div class="abs quote-btn">GET QUOTE</div>
  <h1 class="abs hero-title"><strong>We make awesome educational</strong><span>Videos</span></h1>
  <svg class="abs scroll-btn" width="62" height="62" viewBox="0 0 62 62"><circle cx="31" cy="31" r="29" fill="none" stroke="#fff" stroke-width="2"/><path d="M31 18v24M22 34l9 9 9-9" fill="none" stroke="#fff" stroke-width="2"/></svg>
</header>

<section class="intro">
  <h2>Creating bespoke education videos to showcase schools,<span>colleges &amp; training providers in the north of England</span></h2>
  <div class="abs copy">
    <p>Here at Bracken Learning Films, we know how to create stylish, engaging, and successful educational videos for schools, colleges and training providers. We’ve been making them for years.</p>
    <p>We believe that when you’re trying to attract new learners the best way to show how your learning establishment is better than the rest is with a compelling, top-quality video.</p>
  </div>
  <div class="abs intro-video">
    <div class="media" role="img" aria-label="Aerial drone shot of pupils playing tennis on a red court"></div>
    <svg class="abs" style="left:274px;top:134px" width="44" height="44" viewBox="0 0 44 44"><circle cx="22" cy="22" r="20" fill="none" stroke="#fff" stroke-width="2"/><path d="M17 13l13 9-13 9z" fill="#fff"/></svg>
    <div class="video-label"><strong>SUBJECT VIDEOS</strong>Promote your lessons</div>
  </div>
</section>

<section class="invest">
  <div class="media" role="img" aria-label="Young pupils raising their hands in a classroom"></div>
  <div class="abs body">
    <h3>A one-off investment that<span>brings long-term results</span></h3>
    <p>There are so many ways to repurpose your videos and make the initial investment work for you – sharing snippets on social media, embedding the video onto your website, uploading it to your online video channel or playing it on your welcome screen in reception. The return on investment is excellent (and in some cases, instant!)</p>
    <p><strong>BY THE WAY:</strong> don’t just take our word for how successful our videos are. Check out some of the wonderful feedback we’ve received.</p>
    <a class="btn-dark">READ OUR FEEDBACK</a>
  </div>
</section>

<section class="why">
  <h2>Why Choose<span>Bracken Learning Films</span></h2>
  <div class="card" style="left:138px">
    <div class="badge"><svg width="52" height="52" viewBox="0 0 52 52" fill="none" stroke="#fff" stroke-width="2"><rect x="6" y="18" width="40" height="28" rx="2"/><path d="M6 18l38-8 2 8M14 16l4-7M26 13l4-7"/><path d="M22 26l10 6-10 6z"/></svg></div>
    <h4>EXPERIENCED<br>VIDEO MAKERS</h4>
    <p>We’re a smart bunch of experienced video makers and we know how to create compelling videos that get results.</p>
    <svg class="go" width="36" height="24" viewBox="0 0 36 24" fill="none" stroke="#1db0ee" stroke-width="2"><circle cx="12" cy="12" r="10"/><path d="M8 12h24M27 7l5 5-5 5"/></svg>
  </div>
  <div class="card" style="left:476px">
    <div class="badge"><svg width="52" height="52" viewBox="0 0 52 52" fill="none" stroke="#fff" stroke-width="2"><path d="M6 46h40"/><rect x="10" y="30" width="6" height="16"/><rect x="20" y="22" width="6" height="24"/><rect x="30" y="14" width="6" height="32"/><path d="M8 28l14-10 8 4 14-12"/></svg></div>
    <h4>COST-EFFECTIVE<br>MARKETING</h4>
    <p>We offer a cost-effective marketing solution – no more expensive brochure design-ing, printing and storage hassles.</p>
    <svg class="go" width="36" height="24" viewBox="0 0 36 24" fill="none" stroke="#1db0ee" stroke-width="2"><circle cx="12" cy="12" r="10"/><path d="M8 12h24M27 7l5 5-5 5"/></svg>
  </div>
  <div class="card" style="left:813px">
    <div class="badge"><svg width="52" height="52" viewBox="0 0 52 52" fill="none" stroke="#fff" stroke-width="2"><circle cx="28" cy="30" r="16"/><path d="M28 30V20M28 30l7 4M24 10h8M28 10v4M4 26h8M2 32h10M6 38h8"/></svg></div>
    <h4>SAVE YOU TIME AND<br>EFFORT</h4>
    <p>We save you time and effort – you could invest time, effort and tech into making your own videos, but would they have the same polished?</p>
    <svg class="go" width="36" height="24" viewBox="0 0 36 24" fill="none" stroke="#1db0ee" stroke-width="2"><circle cx="12" cy="12" r="10"/><path d="M8 12h24M27 7l5 5-5 5"/></svg>
  </div>
</section>

<section class="budget" role="img" aria-label="Darkened photo of a student at a desk behind the text">
  <h3>Our Videos Won’t Eat Up All Of Your<span>Marketing Budget Either!</span></h3>
  <p>You see we do things differently at Bracken Learning Films. Our highly experienced and dedicated team is small (but mighty) and that’s how we keep costs low and affordable.</p>
  <a class="btn-blue">VIEW OUR PRICES</a>
</section>

<section class="custom">
  <h2>Creating customised educational videos that<span>exceed your expectations</span></h2>
  <div class="abs custom-video">
    <div class="media" role="img" aria-label="Nursery children in paper crowns planting vegetables with a teacher"></div>
    <svg class="abs" style="left:268px;top:130px" width="44" height="44" viewBox="0 0 44 44"><circle cx="22" cy="22" r="20" fill="none" stroke="#fff" stroke-width="2"/><path d="M17 13l13 9-13 9z" fill="#fff"/></svg>
  </div>
  <div class="abs copy">
    <p>Prefer a prospectus video over a music-driven one? No problem. In fact, we can almost always cater for your specific needs and budgets. All you have to do is ask.</p>
    <p><strong>Our mission</strong> is to capture the heart and soul of your school, college, training company, so your potential recruits can’t resist taking that next step towards enrolling.</p>
    <p>Take a look at our range of video offerings <a>https://brackenlearningfilms.co.uk/our-work/</a></p>
    <a class="btn-outline">WATCH OUR VIDEOS</a>
  </div>
</section>

<section class="drone">
  <div class="abs box">
    <h3>Licensed by the civil aviation authority</h3>
    <p>We Are Licensed Drone Operators Meaning We Can<br>Take To The Sky.</p>
  </div>
  <div class="media" role="img" aria-label="Camera drone in flight"></div>
</section>

<section class="partners">
  <h2>Schools, colleges and training providers<span>we've worked with</span></h2>
  <svg class="arrow" style="left:42px" width="30" height="30" viewBox="0 0 30 30" fill="none" stroke="#888" stroke-width="1.5"><circle cx="15" cy="15" r="13"/><path d="M17 9l-6 6 6 6"/></svg>
  <div class="partner" style="left:128px">Fellside College</div>
  <div class="partner" style="left:395px;font-size:20px;color:#5a8a2a">Meadowbrook Nursery</div>
  <div class="partner" style="left:670px">Linguakids</div>
  <div class="partner" style="left:918px;font-size:18px"><b style="width:32px;height:32px"></b>Hollins Primary</div>
  <svg class="arrow" style="left:1130px" width="30" height="30" viewBox="0 0 30 30" fill="none" stroke="#1db0ee" stroke-width="1.5"><circle cx="15" cy="15" r="13"/><path d="M13 9l6 6-6 6"/></svg>
</section>

<footer>
  <div class="contact" style="left:111px">
    <svg width="28" height="34" viewBox="0 0 28 34" fill="none" stroke="#1db0ee" stroke-width="1.6"><path d="M14 32S3 20 3 12a11 11 0 0 1 22 0c0 8-11 20-11 20z"/><circle cx="14" cy="12" r="4"/></svg>
    <div>Unit 4, Harwood Business Park,<br>Consett, Durham. DH8 2QX.</div>
  </div>
  <div class="contact" style="left:510px">
    <svg width="36" height="36" viewBox="0 0 36 36" fill="none" stroke="#1db0ee" stroke-width="1.6"><path d="M8 3l6 8-3 4c2 5 5 8 10 10l4-3 8 6-3 5C18 33 3 18 3 6z"/></svg>
    <div>Phone:<br>07700 900 318</div>
  </div>
  <div class="contact" style="left:744px">
    <svg width="38" height="30" viewBox="0 0 38 30" fill="none" stroke="#1db0ee" stroke-width="1.6"><rect x="2" y="4" width="34" height="24" rx="2"/><path d="M2 6l17 12L36 6"/></svg>
    <div>Email:<br>info@brackenlearningfilms.co.uk</div>
  </div>
  <div class="rule" style="top:179px"></div>
  <nav class="foot-nav"><span>Home</span><span>About</span><span>Prices</span><span>Testimonials</span><span>Contact Page</span><span>Promotional Videos</span><span>Subject Videos</span></nav>
  <div class="rule" style="top:272px"></div>
  <div class="copyright">2023 Bracken Learning Films Limited. All Rights Reserved.</div>
  <div class="social"></div>
</footer>

</body>
</html>
```